House Cleaning Platform for Consumers and Cleaners

UPDATE: I've attached screenshots showing a purchase flow example, something all designers have missed in their designs. PLEASE check the URLs I've included in the brief for examples of a cleaning website. I've seen mostly landing pages and nothing else.

WHAT I'M LOOKING FOR:
I need the UI designed for a house cleaning web platform from 2 separate experiences: one from the consumer end to order a cleaner to come clean their house and one from a cleaner’s end that manages their orders and manages their schedule.

The UI will need to include photo uploading for before and after photos, a checkout/cart experience w/ tips, toggle options for adding and removing rooms/extras cleaning add-ons, customer+cleaner reviews (meaning the cleaner finished the job and they can rate and review the customer as well as the customer can rate and review the cleaner), order history for consumers, job history for cleaners, profile, settings, and landing pages for both.

PLEASE DO NOT USE THE COLOR BLUE AS THE PRIMARY COLOR. Use a light green (HEX #2fdf86) instead for primary theming color.

REFERENCES:
If you'd like a few websites I've enjoyed for references, checkout:
larkpolish.example, vomby.example, and brightfernhome.example.

For sake of branding, the company name is PlumNest. Currently do not have a logo as we have not decided on the name. Logo will come later.

Feel free to reach out to me if you have any questions!
Updates

Most designer submissions were a landing page and only a landing page. Very few designed the flows I requested and none designed a schedule management page. I even updated the Brief to more clearly outline the needs and references. Only about 2-3 of the designers actually did more than a landing page. Still don't believe I received 6 designers input that I had paid for.

Target Market(s)

FULL-TIME WORKING HOUSEHOLDS, SINGLE PROFESSIONALS, SINGLE PARENTS, ELDERLY & MOBILITY CHALLENGED, BUSY BODIES.

Industry/Entity Type

Cleaning, gig work.

Number of Pages Required

5+ page

Font styles to use
Other font styles liked:
• Jost or Lexend are great Google Font options I've used in the pitch deck and horribly done app mockups.

Colors
00AB8E
00BBA5
67D7C9
C6EFE9
E9F9F6
59FF00
82FF00
B8FF75
E3FFCB
F4FFEA
FFF300
FFF600
FEFA6F
FFFEC7
FFFEE8
FFC000
F8CF3A
FAE287
FDF2CF
FEFAEE

Requirements
Must have
• Landing page, consumer flow, cleaner schedule management, checkout flow, Rate & Review for consumer and/or cleaner, order history, profile.
Nice to have
• I'd like it to be simple in design and modern, but not so simple it's boring. Iconography can sometimes break that up, but I don't want it looking busy. It's a cleaning platform so the UI should look clean.

```html
<!DOCTYPE html>
<html lang="en">
<head>
<meta charset="utf-8">
<title>PlumNest – Book Your Services</title>
<link href="https://fonts.googleapis.com/css2?family=Open+Sans:wght@400;600;700;800&display=swap" rel="stylesheet">
<style>
:root{
  --green:#2fdf86;
  --orange:#f5a524;
  --ink:#1d1d1d;
  --muted:#8a8a8a;
  --line:#e6e6e6;
  --field:#dcdcdc;
  --dark:#3a3a3a;
  --bg:#ffffff;
}
*{box-sizing:border-box;margin:0;padding:0}
html,body{width:1200px;height:3896px;overflow:hidden;background:var(--bg)}
body{font-family:"Open Sans",Arial,sans-serif;color:var(--ink)}
.page{width:1200px;height:3896px;overflow:hidden;position:relative}

.site-header{height:64px;display:flex;align-items:center;justify-content:space-between;padding:0 40px}
.brand{display:flex;align-items:center;gap:10px;font-size:28px;font-weight:800;color:var(--green)}
.brand-dot{width:12px;height:12px;border-radius:50%;background:var(--green)}
.main-nav{display:flex;align-items:center;gap:26px;font-size:13px;font-weight:600}
.search{display:flex;align-items:center;gap:8px;width:200px;height:30px;border:1px solid var(--field);border-radius:4px;padding:0 10px;color:var(--muted);font-size:12px;font-weight:400}
.btn-signup{background:var(--green);color:#fff;border-radius:16px;padding:6px 16px}

.page-title{text-align:center;font-size:40px;font-weight:700;padding:68px 0 30px;border-bottom:1px solid var(--line)}

.content{padding:0 96px}
.summary-title{color:var(--orange);font-size:30px;font-weight:700;padding:44px 0 26px;border-bottom:1px solid var(--line)}
.summary{display:grid;grid-template-columns:1fr 1fr;padding:48px 0 40px;border-bottom:1px solid var(--line)}
.summary-col{display:flex;gap:56px}
.summary-col+.summary-col{border-left:1px solid var(--line);padding-left:40px}
.summary-label{font-size:20px;font-weight:700}
.summary-price{font-size:30px;font-weight:800;margin-top:-6px}
.summary ul{list-style:none;margin-top:14px;font-size:12px;color:#555}
.summary li{padding-left:14px;position:relative;line-height:22px}
.summary li::before{content:"";position:absolute;left:0;top:9px;width:5px;height:5px;border-radius:50%;background:var(--green)}

.row{display:grid;grid-template-columns:452px 452px;column-gap:104px}
.block{margin-top:52px}
.label{font-size:20px;font-weight:700}
.help{font-size:11px;color:var(--muted);margin:8px 0 14px;line-height:16px}
.field{height:40px;border:1px solid var(--field);border-radius:4px;padding:0 14px;display:flex;align-items:center;justify-content:space-between;font-size:12px;color:#aaa}
.field.dark{color:var(--ink)}
.caret{width:0;height:0;border-left:5px solid transparent;border-right:5px solid transparent;border-top:6px solid var(--ink)}

.radios{display:flex;gap:56px;font-size:12px}
.radio{display:flex;align-items:center;gap:10px}
.dot{width:14px;height:14px;border:1px solid #bbb;border-radius:50%;display:inline-block;position:relative;flex:none}
.dot.on{border-color:var(--green)}
.dot.on::after{content:"";position:absolute;inset:3px;border-radius:50%;background:var(--green)}

.opt{height:40px;border:1px solid var(--field);border-radius:4px;display:flex;align-items:center;gap:12px;padding:0 14px;font-size:12px;margin-bottom:12px}
.opt .note{margin-left:auto;font-size:10px;color:#bbb}
.opt .qty{margin-left:auto;display:flex;align-items:center;gap:6px;font-size:11px}
.hint{font-size:11px;color:var(--muted);display:flex;align-items:center;gap:6px}
.hint b{color:var(--orange);font-weight:600}
.check{display:flex;align-items:center;gap:10px;font-size:11px;margin-top:4px}
.box{width:14px;height:14px;border-radius:50%;background:var(--green);display:inline-flex;align-items:center;justify-content:center}
.help-row{display:flex;gap:8px}

.freq-head{display:flex;align-items:center;gap:12px}
.freq{display:grid;grid-template-columns:repeat(4,1fr);gap:24px;margin-top:24px;padding-right:0}
.card{border:1px solid var(--field);border-radius:6px;overflow:hidden;height:388px}
.card-top{height:76px;background:var(--dark);color:#fff;font-size:26px;font-weight:800;display:flex;align-items:center;justify-content:center}
.card.active .card-top{background:var(--green)}
.card-body{padding:30px 22px;text-align:center}
.card-body h4{font-size:17px;font-weight:700;margin-bottom:14px}
.card-body p{font-size:11px;color:#666;line-height:16px}

.sub{font-size:12px;font-weight:600;margin:18px 0 8px}
.section-head{font-size:20px;font-weight:700}
.area{height:92px;border:1px solid var(--field);border-radius:4px}
.coupon{display:flex;gap:0}
.coupon .field{flex:1;border-radius:4px 0 0 4px}
.apply{width:100px;height:40px;display:flex;align-items:center;justify-content:center;font-size:12px;font-weight:600;border-radius:0 4px 4px 0}
.apply.on{background:var(--orange);color:#fff}
.apply.off{background:#ddd;color:#fff}

.actions{display:flex;gap:60px;margin-top:52px}
.btn{width:140px;height:48px;border-radius:24px;display:flex;align-items:center;justify-content:center;font-size:15px;font-weight:700}
.btn-back{border:1px solid var(--field)}
.btn-pay{background:var(--green);color:#fff;width:180px}
</style>
</head>
<body>
<div class="page">
  <header class="site-header">
    <div class="brand"><span class="brand-dot"></span>PlumNest</div>
    <nav class="main-nav">
      <span>Home</span><span>Pricing</span><span>Services</span><span>Contact</span><span>Help</span>
      <span class="search"><svg width="12" height="12" viewBox="0 0 12 12"><circle cx="5" cy="5" r="4" fill="none" stroke="#888" stroke-width="1.5"/><line x1="8" y1="8" x2="11" y2="11" stroke="#888" stroke-width="1.5"/></svg>Search</span>
      <span>Login</span><span class="btn-signup">Sign Up</span>
    </nav>
  </header>

  <h1 class="page-title">Book Your Services Now</h1>

  <main class="content">
    <h2 class="summary-title">Booking Summary</h2>
    <section class="summary">
      <div class="summary-col">
        <div><div class="summary-label">First Clean</div>
          <ul><li>Deep Cleaning</li><li>Inside Fridge</li><li>Inside Oven</li></ul></div>
        <div class="summary-price">$314.00</div>
      </div>
      <div class="summary-col">
        <div><div class="summary-label">Recurring Cleans</div>
          <ul><li>Standard Cleaning</li><li>Weekly</li><li>15% discount</li></ul></div>
        <div class="summary-price">$126.65</div>
      </div>
    </section>

    <div class="row block">
      <div><div class="label">Enter Property Zip Code</div>
        <p class="help">The zip code helps us to give accurate quote and pricing details.</p>
        <div class="field">Enter zip</div></div>
      <div><div class="label">Total Square Feet At Home</div>
        <p class="help">Enter your total square feet at your home. The number will be verified by our system.</p>
        <div class="field">Square footage</div></div>
    </div>

    <div class="row block">
      <div><div class="label">How Many Bedrooms?</div>
        <p class="help">Enter total number of bedrooms in the home. You can Exclude number of Bedrooms on a later step.</p>
        <div class="field">Select bedrooms<span class="caret"></span></div></div>
      <div><div class="label">How Many Bathrooms?</div>
        <p class="help">Enter total number of bathrooms in the home. Round half baths up (this will not affect price). You can Exclude Bathrooms at a later step.</p>
        <div class="field">Select bathrooms<span class="caret"></span></div></div>
    </div>

    <div class="block"><div class="label">Any Pets At Home?</div>
      <p class="help">This reminds you and our staff that there is or is not pets in the home. Select any one.</p>
      <div class="radios">
        <span class="radio"><span class="dot on"></span>No pets in the home</span>
        <span class="radio"><span class="dot"></span>Dog(s)</span>
        <span class="radio"><span class="dot"></span>Cat(s)</span>
        <span class="radio"><span class="dot"></span>Dog(s) and Cat(s)</span>
      </div></div>

    <div class="block"><div class="label">Do You Want To Exclude Any Bathrooms Or Bedrooms?</div>
      <p class="help">If you don't want some rooms to cleaned, indicate that below. Excluding rooms will be calculated into the quote.</p>
      <div class="row">
        <div><div class="opt"><span class="dot on"></span>Exclude Bedroom(s)<span class="qty">1 <span class="caret"></span></span></div>
          <div class="opt"><span class="dot"></span>Do not exclude any rooms</div></div>
        <div><div class="opt"><span class="dot"></span>Exclude Bathroom(s)</div></div>
      </div></div>

    <div class="block"><div class="label">Condition Of Home</div>
      <div class="help-row help"><span>Select the condition that is most accurate.</span><span class="hint"><b>●</b> Most suitable guideline</span></div>
      <div class="help-row help" style="margin-top:-8px"><span>Some home conditions are not acceptable.</span><span class="hint"><b>●</b> See the guideline</span></div>
      <div class="row">
        <div><div class="opt"><span class="dot on"></span>Heavy dusty condition<span class="note">?</span></div>
          <div class="opt"><span class="dot"></span>Good or Green condition<span class="note">?</span></div></div>
        <div><div class="opt"><span class="dot"></span>Average to Good condition<span class="note">?</span></div></div>
      </div>
      <div class="check"><span class="box"><svg width="8" height="8" viewBox="0 0 8 8"><path d="M1 4l2 2 4-4" fill="none" stroke="#fff" stroke-width="1.5"/></svg></span>I've read all the conditions carefully</div></div>

    <div class="block"><div class="label">Type Of Cleaning</div>
      <p class="help">View and compare cleaning checklists below. Please review the excluded services list so your no not included.</p>
      <div class="row">
        <div class="opt"><span class="dot on"></span>Deep Cleaning<span class="note">View checklist</span></div>
        <div class="opt"><span class="dot"></span>Move In/Out Cleaning<span class="note">View checklist</span></div>
      </div></div>

    <div class="block"><div class="label">Add-On Services <span class="hint" style="display:inline-flex;font-weight:400"><b>●</b></span></div>
      <p class="help">These are extras that can be included in addition to the cleaning checklist.</p>
      <div class="row">
        <div><div class="opt"><span class="dot"></span>Inside Fridge</div><div class="opt"><span class="dot"></span>Wipe Baseboard</div><div class="opt"><span class="dot"></span>Interior Windows</div></div>
        <div><div class="opt"><span class="dot"></span>Inside Cabinets</div><div class="opt"><span class="dot"></span>Inside Oven</div><div class="opt"><span class="dot"></span>Wet Wipe Blinds</div></div>
      </div>
      <div class="check"><span class="box"><svg width="8" height="8" viewBox="0 0 8 8"><path d="M1 4l2 2 4-4" fill="none" stroke="#fff" stroke-width="1.5"/></svg></span>I've read all the checklists carefully</div></div>

    <div class="block">
      <div class="freq-head"><svg width="18" height="18" viewBox="0 0 18 18"><rect x="2" y="3" width="14" height="13" rx="2" fill="none" stroke="#ccc" stroke-width="1.5"/></svg><span class="label">Frequency</span></div>
      <p class="help">How often do you want services?</p>
      <div class="freq">
        <div class="card"><div class="card-top">10% Discount</div><div class="card-body"><h4>Every Two Weeks</h4><p>Regular tidy visits every second week keep dust, floors and kitchen surfaces under control with a steady routine for busy homes.</p></div></div>
        <div class="card"><div class="card-top">5% Discount</div><div class="card-body"><h4>Every Four Weeks</h4><p>A monthly visit for homes that stay fairly neat but need a fresh reset of bathrooms, floors and shared living spaces.</p></div></div>
        <div class="card active"><div class="card-top">15% Discount</div><div class="card-body"><h4>Weekly</h4><p>Our best value plan with the same cleaner each week, ideal for families, pets and anyone who wants a spotless home.</p></div></div>
        <div class="card"><div class="card-top">No Discount</div><div class="card-body"><h4>One Time</h4><p>A single visit for events, guests or a seasonal refresh, booked once with no ongoing plan or commitment.</p></div></div>
      </div>
    </div>

    <div class="block"><div class="label">Date Of Cleaning</div>
      <p class="help">Choose from available appointment times. Please note there is a 1 hour arrival window.</p>
      <div class="field" style="width:452px">Select a date<svg width="14" height="14" viewBox="0 0 14 14"><rect x="1" y="2" width="12" height="11" rx="1.5" fill="none" stroke="#555"/><line x1="1" y1="5" x2="13" y2="5" stroke="#555"/></svg></div></div>

    <div class="block"><div class="section-head">Address Details</div>
      <div class="row"><div><div class="sub">Property Address</div><div class="field">Street address</div></div><div><div class="sub">Apartment Or Suite #</div><div class="field">Apt / Suite</div></div></div>
      <div style="display:grid;grid-template-columns:1fr 1fr 1fr;gap:40px"><div><div class="sub">City</div><div class="field">City</div></div><div><div class="sub">State</div><div class="field">State<span class="caret"></span></div></div><div><div class="sub">Zip Code</div><div class="field">Zip</div></div></div>
      <div class="sub">Notes Or Special Instructions?</div><div class="area"></div></div>

    <div class="block"><div class="section-head">Contact Information</div>
      <div class="row"><div><div class="sub">First Name</div><div class="field">First name</div></div><div><div class="sub">Last Name</div><div class="field">Last name</div></div></div>
      <div class="row"><div><div class="sub">Email</div><div class="field">Email</div></div><div><div class="sub">Phone</div><div class="field">Phone</div></div></div></div>

    <div class="block" style="margin-top:44px"><div class="section-head">Other Details</div>
      <div class="sub">How Did You Hear About Us?</div><div class="field">Select an option<span class="caret"></span></div>
      <div class="row"><div><div class="sub">Enter Coupon Code</div><div class="coupon"><div class="field dark">SAVE10</div><div class="apply on">Apply</div></div></div>
        <div><div class="sub">Enter Coupon Code</div><div class="coupon"><div class="field">Code</div><div class="apply off">Apply</div></div></div></div></div>

    <div class="actions"><div class="btn btn-back">Back</div><div class="btn btn-pay">Make Payment</div></div>
  </main>
</div>
</body>
</html>
```